A modern, fresh introduction to Buddhism

I need a book cover for an A6 sized book to be used both for ebook and hard copy. The author is a young, modern Buddhist teacher of high standing who has written this short intro to Buddhism in an informal Q & As format using modern, accessible language to convey profound and meaningful ideas to the general public. The author is Tibetan, but teaches worldwide and is very personable and dynamic. The cover should portray this and have a fresh yet authentic feel to it (nothing new-agey!). Please see the author's websites www.torvenmalsiteacher.org and www.vrmq.org for reference, but do not feel that the design must align completely with the website designs.

Target Market(s)

General public both in Europe and America and in Asia ranging from teenagers to the elderly. A really broad audience.

Industry/Entity Type

Teacher

Requirements
Must have
• Please include the following text that on the front cover:

A Window Onto Stillwaters

By Dorwel Tamsung Geshela

Please include the following on the back cover:

Mirun Teskavo Publications (with attached logo above it)
Nice to have
• A simplistic, artistic, and modern look without any traditional religious images.
Should not have
• No buddha images or religious images. I would prefer a more simplistic, modern and artistic look.

```html
<!DOCTYPE html>
<html lang="en">
<head>
<meta charset="utf-8">
<title>A Window Onto Stillwaters — Dorwel Tamsung Geshela</title>
<link href="https://fonts.googleapis.com/css2?family=Playfair+Display:ital,wght@1,600&family=Cabin:wght@400&display=swap" rel="stylesheet">
<style>
  :root {
    --deep-plum: #2a0426;
    --plum: #5e0f4e;
    --magenta: #b3236f;
    --rose: #e8889a;
    --glow: #fff4e6;
    --title-ink: #6a1466;
    --band: rgba(98, 18, 104, 0.92);
    --band-text: #ffffff;
    --author: #f08cbc;
  }
  html, body {
    margin: 0;
    padding: 0;
    width: 848px;
    height: 1200px;
    overflow: hidden;
    background: var(--deep-plum);
  }
  .cover {
    position: relative;
    width: 848px;
    height: 1200px;
    overflow: hidden;
  }
  .light-burst {
    position: absolute;
    inset: 0;
    background:
      radial-gradient(ellipse 38% 30% at 50% 56%, var(--glow) 0%, rgba(255,236,220,0.85) 25%, rgba(240,150,150,0.4) 60%, transparent 100%),
      radial-gradient(ellipse 75% 60% at 50% 56%, var(--rose) 0%, var(--magenta) 45%, var(--plum) 75%, var(--deep-plum) 100%);
  }
  .title {
    position: absolute;
    left: 0;
    right: 0;
    top: 498px;
    margin: 0;
    text-align: center;
    font-family: "Playfair Display", serif;
    font-style: italic;
    font-weight: 600;
    font-size: 84px;
    line-height: 106px;
    color: var(--title-ink);
  }
  .title-line { display: block; }
  .subtitle-band {
    position: absolute;
    left: 0;
    right: 0;
    top: 744px;
    height: 59px;
    background: var(--band);
    display: flex;
    align-items: center;
    justify-content: center;
  }
  .subtitle {
    margin: 0;
    font-family: "Cabin", sans-serif;
    font-weight: 400;
    font-size: 33px;
    color: var(--band-text);
    letter-spacing: 0.2px;
  }
  .author {
    position: absolute;
    left: 0;
    right: 0;
    top: 1094px;
    margin: 0;
    text-align: center;
    font-family: "Cabin", sans-serif;
    font-size: 30px;
    line-height: 36px;
    color: var(--author);
  }
</style>
</head>
<body>
  <main class="cover">
    <div class="light-burst" role="img" aria-label="Radiant burst of magenta and purple light rays spreading from a bright centre"></div>
    <h1 class="title">
      <span class="title-line">A Window Onto</span>
      <span class="title-line">Stillwaters</span>
    </h1>
    <div class="subtitle-band">
      <p class="subtitle">A Short Introduction to the Buddha's Teaching</p>
    </div>
    <p class="author">Dorwel Tamsung Geshela</p>
  </main>
</body>
</html>
```